Business Card Design

We need a business card designed for our new company. Prefer a black card with white logo & writing.

Contact Information for Business Card

Ted Galloway, address: 7-4812 Fernhollow Road, Abbotsford, BC, V3K 8R2, Office Phone: 604-712-3390, Cell: 604-947-2164, Email: ted@resinworkshub.ca

Colors

Designer to choose only greyscale colors for use in the design.

```html
<!DOCTYPE html>
<html lang="en">
<head>
<meta charset="utf-8">
<title>Resinworks Hub — Business Card</title>
<link rel="stylesheet" href="https://fonts.googleapis.com/css2?family=Poppins:wght@300;400;700&display=swap">
<style>
  :root {
    --stage: #2b2b2b;
    --card: #1f1f21;
    --ink: #ffffff;
    --ink-soft: #d9d9d9;
  }
  * { box-sizing: border-box; margin: 0; padding: 0; }
  html, body { width: 1200px; height: 780px; overflow: hidden; }
  body {
    background: var(--stage);
    font-family: "Poppins", sans-serif;
    color: var(--ink);
    position: relative;
  }
  .card {
    position: absolute;
    top: 240px;
    width: 520px;
    height: 300px;
    background: var(--card);
    border-radius: 4px;
    box-shadow: 0 10px 30px rgba(0,0,0,.45);
    overflow: hidden;
  }
  .card--back { left: 50px; }
  .card--front { left: 630px; display: flex; align-items: center; justify-content: center; }

  .brand {
    display: flex;
    align-items: center;
    gap: 10px;
    font-weight: 700;
    text-transform: uppercase;
    letter-spacing: .04em;
    line-height: 1;
    color: var(--ink);
  }
  .brand__mark { border: 3px solid var(--ink); display: inline-block; }
  .card--front .brand { font-size: 40px; }
  .card--front .brand__mark { width: 34px; height: 34px; }

  .card--back .brand { position: absolute; left: 34px; top: 34px; font-size: 22px; }
  .card--back .brand__mark { width: 20px; height: 20px; border-width: 2px; }

  .address {
    position: absolute;
    left: 34px;
    top: 84px;
    font-size: 12px;
    font-weight: 300;
    line-height: 1.45;
    color: var(--ink-soft);
  }
  .contacts {
    position: absolute;
    left: 34px;
    top: 132px;
    list-style: none;
    font-size: 12px;
    font-weight: 300;
    line-height: 1.6;
    color: var(--ink-soft);
  }
  .contacts li { display: flex; align-items: center; gap: 8px; }
  .contacts svg { width: 12px; height: 12px; flex: none; }

  .person {
    position: absolute;
    right: 40px;
    top: 196px;
    text-align: right;
  }
  .person__name { font-size: 32px; font-weight: 300; line-height: 1.05; }
  .person__name strong { font-weight: 700; }
  .person__role { font-size: 14px; font-weight: 300; color: var(--ink-soft); margin-top: 2px; }
  .accent-bar {
    position: absolute;
    right: 0;
    top: 196px;
    width: 16px;
    height: 62px;
    background: var(--ink);
  }
</style>
</head>
<body>
  <section class="card card--back" aria-label="Business card, contact side">
    <div class="brand"><span class="brand__mark"></span>Resinworks Hub</div>
    <p class="address">7-4812 Fernhollow Road,<br>Abbotsford, BC, V3K 8R2.</p>
    <ul class="contacts">
      <li>
        <svg viewBox="0 0 24 24" fill="#fff" aria-hidden="true"><path d="M6.6 10.8a15.1 15.1 0 0 0 6.6 6.6l2.2-2.2c.3-.3.7-.4 1-.2 1.1.4 2.3.6 3.6.6.6 0 1 .4 1 1V20c0 .6-.4 1-1 1C10.6 21 3 13.4 3 4c0-.6.4-1 1-1h3.5c.6 0 1 .4 1 1 0 1.3.2 2.5.6 3.6.1.3 0 .7-.2 1z"/></svg>
        604-712-3390
      </li>
      <li>
        <svg viewBox="0 0 24 24" fill="none" stroke="#fff" stroke-width="2" aria-hidden="true"><rect x="6" y="2" width="12" height="20" rx="2"/><circle cx="12" cy="18" r="1" fill="#fff"/></svg>
        604-947-2164
      </li>
      <li>
        <svg viewBox="0 0 24 24" fill="none" stroke="#fff" stroke-width="2" aria-hidden="true"><circle cx="12" cy="12" r="9"/><path d="M3 12h18M12 3c3 3 3 15 0 18M12 3c-3 3-3 15 0 18"/></svg>
        www.resinworkshub.ca
      </li>
      <li>
        <svg viewBox="0 0 24 24" fill="none" stroke="#fff" stroke-width="2" aria-hidden="true"><rect x="3" y="5" width="18" height="14" rx="1"/><path d="M3 6l9 7 9-7"/></svg>
        ted@resinworkshub.ca
      </li>
    </ul>
    <div class="person">
      <p class="person__name"><strong>Ted</strong> Galloway</p>
      <p class="person__role">Founder &amp; CEO</p>
    </div>
    <span class="accent-bar"></span>
  </section>

  <section class="card card--front" aria-label="Business card, logo side">
    <div class="brand"><span class="brand__mark"></span>Resinworks Hub</div>
  </section>
</body>
</html>
```